Brackenford Fluidworks needs a website describing the repair business we are in.

Brackenford Fluidworks is a full hydraulic repair facility. We have 2 shops. We repair and service all hydraulic cylinders, pneumatic cylinders, hydraulic pumps, motors, valves and gearboxes. Our services range from large industrial plants to the individual that owns one piece of equipment. We also offer removal and install of cylinders. Along with free pick up and delivery, within a certain distance which is usually 100 miles from one of our shops.

With over 30 years experience in the hydraulic business, we can repair or replace any job. There is not a job too big or too small, we service them all.

We have customers that send whole pieces of equipment to us to do complete overhauls on all the hydraulics. Ranging from a country club green roller to a 10 ton boom truck.

Target Market(s)

Industrial plants, road builders, dirt work companies, general contractors, owners of industrial equipment (bulldozers, excavators, loaders, scrapers, motor graders, etc.

Industry/Entity Type

Hydraulic

Number of Pages Required

5+ page

Font styles to use
Sans Serif

Colors
ec1f27
ffffff
aaaaaa

Requirements
Must have
• Information about what we offer and pictures of jobs completed.
Nice to have
• Nice stock photos of jobsites and industrial plants.
Should not have
• Any sort of comical characters.

```html
<!DOCTYPE html>
<html lang="en">
<head>
<meta charset="utf-8">
<title>Brackenford Fluidworks — Hydraulic Repair</title>
<link rel="stylesheet" href="https://fonts.googleapis.com/css2?family=Montserrat:wght@400;500;600;700&family=Arimo:wght@400;700&display=swap">
<style>
:root{
  --red:#ec1f27;
  --red-dark:#c8141b;
  --white:#ffffff;
  --grey:#aaaaaa;
  --ink:#1d1d1f;
  --text:#333333;
  --navy:#1d3f72;
  --sky:#1da1f2;
}
*{margin:0;padding:0;box-sizing:border-box}
html,body{width:1200px;height:2341px;overflow:hidden;background:var(--white)}
body{font-family:"Arimo",Arial,sans-serif;color:var(--text)}
.canvas{position:relative;width:1200px;height:2341px;overflow:hidden;background:var(--white)}
.abs{position:absolute}
.heading{font-family:"Montserrat",Arial,sans-serif}

/* hero */
.hero-art{position:absolute;left:0;top:0}
.brand{position:absolute;left:72px;top:28px;display:flex;align-items:center;gap:10px}
.brand-dot{width:30px;height:30px;border-radius:50%;background:var(--red)}
.brand-name{font-family:"Montserrat",Arial,sans-serif;font-weight:700;color:var(--red);font-size:17px;line-height:20px;letter-spacing:.5px}
.nav{position:absolute;top:48px;left:382px;display:flex;gap:0}
.nav a{position:absolute;white-space:nowrap;font-family:"Montserrat",Arial,sans-serif;font-weight:600;font-size:15px;color:var(--white);text-decoration:none}
.nav .active::after{content:"";position:absolute;left:-2px;top:31px;width:62px;height:4px;background:var(--red);border-radius:2px}
.call{position:absolute;left:922px;top:0;width:219px;height:86px;background:var(--red);color:var(--white);display:flex;align-items:center;padding-left:18px;gap:16px}
.call-label{font-family:"Montserrat",Arial,sans-serif;font-weight:600;font-size:14px;line-height:16px}
.call-number{font-family:"Montserrat",Arial,sans-serif;font-weight:700;font-size:22px;line-height:26px}
.social-rail{position:absolute;left:1162px;top:168px;width:38px}
.social-rail span{display:block;height:40px;margin-bottom:10px}
.hero-title{position:absolute;left:0;width:1200px;top:300px;text-align:center;font-family:"Montserrat",Arial,sans-serif;font-weight:700;font-size:96px;color:var(--white);letter-spacing:2px;line-height:110px}
.hero-sub{position:absolute;left:400px;top:410px;width:402px;height:42px;background:rgba(30,30,30,.6);color:var(--white);text-align:center;font-family:"Montserrat",Arial,sans-serif;font-weight:500;font-size:25px;line-height:42px;letter-spacing:3px}

/* welcome */
.welcome{position:absolute;left:0;top:670px;width:1200px;text-align:center}
.eyebrow{font-family:"Montserrat",Arial,sans-serif;font-weight:600;font-size:17px;color:var(--ink);display:flex;justify-content:center;align-items:center;gap:18px;letter-spacing:1px}
.eyebrow::before,.eyebrow::after{content:"";width:44px;height:1px;background:var(--ink)}
.welcome h1{font-family:"Montserrat",Arial,sans-serif;font-weight:600;color:var(--red);font-size:31px;margin-top:16px;letter-spacing:.5px}
.welcome p{width:1030px;margin:14px auto 0;font-size:14.6px;line-height:33px;color:var(--ink)}
.btn{display:inline-block;background:var(--red);color:var(--white);font-family:"Montserrat",Arial,sans-serif;font-weight:500;text-decoration:none;text-align:center}
.welcome .btn{width:176px;height:50px;line-height:50px;font-size:23px;margin-top:20px}

/* services */
.services-head{position:absolute;left:0;width:1200px;top:1136px;text-align:center;color:var(--white)}
.services-head h2{font-family:"Montserrat",Arial,sans-serif;font-weight:500;font-size:30px;letter-spacing:1px}
.services-head p{font-weight:700;font-size:25px;margin-top:8px}
.job{position:absolute;top:1248px;width:306px;height:208px;border:2px solid var(--white)}
.arrow{position:absolute}

/* blog */
.blog-title{position:absolute;left:0;width:1200px;top:1544px;text-align:center;font-family:"Montserrat",Arial,sans-serif;font-weight:600;font-size:33px;color:var(--red)}
.post{position:absolute;top:1617px;width:330px}
.post-photo{position:relative;width:330px;height:263px}
.post-author{position:absolute;left:0;top:0;width:150px;height:37px;background:var(--red);clip-path:polygon(0 0,100% 0,86% 100%,0 100%);color:var(--white);font-weight:700;font-size:13px;line-height:37px;padding-left:18px}
.post-date{position:absolute;right:12px;top:162px;width:77px;height:89px;background:var(--white);text-align:center;color:var(--ink);font-family:"Montserrat",Arial,sans-serif;font-weight:700}
.post-date .d{font-size:33px;line-height:40px;margin-top:6px}
.post-date .m{font-size:19px;line-height:20px}
.post-date .y{font-size:12px;line-height:18px}
.post p{margin-top:18px;font-size:18px;line-height:25px;color:#111;text-align:justify}
.post .btn{width:130px;height:36px;line-height:36px;font-size:18px;margin-top:23px}

/* footer */
.footer-rule{position:absolute;left:0;top:2050px;width:1200px;height:5px;background:var(--red)}
.foot-brand{position:absolute;left:75px;top:2100px;display:flex;align-items:center;gap:10px}
.foot-brand .brand-name{font-size:18px;line-height:22px}
.foot-address{position:absolute;left:75px;top:2219px;font-size:14px;line-height:22px;color:#111;padding-left:24px}
.foot-address svg{position:absolute;left:0;top:4px}
.copyright{position:absolute;left:75px;top:2282px;font-size:13px;color:#555}
.foot-col h3{font-family:"Montserrat",Arial,sans-serif;font-weight:600;font-size:17px;color:var(--ink);letter-spacing:.5px}
.links{list-style:none;margin-top:16px}
.links li{font-size:13.5px;color:#111;height:33px;display:flex;align-items:center;gap:12px}
.links li::before{content:"";width:6px;height:6px;border-right:2px solid #111;border-top:2px solid #111;transform:rotate(45deg)}
.email{margin-top:22px;width:236px;height:35px;background:#dcdcdc;display:flex;align-items:center;justify-content:space-between;padding:0 16px 0 20px;font-size:13px;font-weight:700;color:#666}
.subscribe{margin-top:10px;width:145px;height:36px;line-height:36px;font-size:17px;letter-spacing:1px}
.foot-social{display:flex;gap:7px;margin-top:14px}
.foot-social span{width:40px;height:40px;display:block}
.about-text{margin-top:16px;width:273px;font-size:15px;line-height:22px;color:#111;text-align:justify}
.about-btn{margin-top:12px;width:94px;height:27px;line-height:27px;font-size:13.5px}
</style>
</head>
<body>
<div class="canvas">

  <!-- hero artwork -->
  <svg class="hero-art" width="1200" height="690" viewBox="0 0 1200 690">
    <defs>
      <radialGradient id="sun" cx="0.52" cy="0.28" r="0.75">
        <stop offset="0" stop-color="#fff3c4"/>
        <stop offset="0.18" stop-color="#f3b25e"/>
        <stop offset="0.45" stop-color="#8b6a52"/>
        <stop offset="0.75" stop-color="#3c4556"/>
        <stop offset="1" stop-color="#1c2330"/>
      </radialGradient>
    </defs>
    <polygon points="0,0 1200,0 1200,672 0,578" fill="url(#sun)" role="img" aria-label="Photo of an oil refinery with tall towers at sunset, a ship in the foreground"/>
    <polygon points="0,578 1200,672 1200,678 0,584" fill="var(--red)"/>
  </svg>

  <header>
    <div class="brand"><span class="brand-dot"></span><span class="brand-name">BRACKENFORD<br>FLUIDWORKS</span></div>
    <nav class="nav">
      <a class="active" style="left:0">HOME</a>
      <a style="left:86px">ABOUT US</a>
      <a style="left:205px">SERVCES</a>
      <a style="left:312px">BLOG</a>
      <a style="left:395px">CONTACT US</a>
    </nav>
    <div class="call">
      <svg width="16" height="26" viewBox="0 0 16 26"><rect x="1.5" y="1.5" width="13" height="23" rx="2.5" fill="none" stroke="#fff" stroke-width="2.5"/><circle cx="8" cy="20" r="1.6" fill="#fff"/></svg>
      <div><div class="call-label">CALL US</div><div class="call-number">1-800 555 0142</div></div>
    </div>
  </header>

  <div class="social-rail">
    <span style="background:var(--navy)"></span>
    <span style="background:var(--sky)"></span>
    <span style="background:var(--red)"></span>
  </div>

  <div class="hero-title">LORIUM</div>
  <div class="hero-sub">Ipsum Dolor Amit sed</div>
  <svg class="arrow" style="left:578px;top:545px" width="44" height="18" viewBox="0 0 44 18"><path d="M10 3 L4 9 L10 15" fill="none" stroke="#fff" stroke-width="2.5"/><path d="M34 3 L40 9 L34 15" fill="none" stroke="#fff" stroke-width="2.5"/></svg>

  <!-- welcome backdrop -->
  <div class="abs" role="img" aria-label="Faint grey photo of an industrial plant skyline" style="left:0;top:640px;width:1200px;height:430px;background:linear-gradient(180deg,#ffffff 0%,#eeeeee 45%,#e2e2e2 80%,#f3f3f3 100%);z-index:-0"></div>
  <svg class="hero-art" style="top:578px" width="1200" height="100" viewBox="0 0 1200 100"><polygon points="0,6 1200,100 1200,0 0,0" fill="none"/></svg>

  <section class="welcome">
    <div class="eyebrow">WELCOME TO</div>
    <h1>BRACKENFORD FLUIDWORKS</h1>
    <p>Brackenford Fluidworks is a full hydraulic repair facility. We have 2 shops. We repair and service all hydraulic cylinders, pneumatic cylinders, hydraulic pumps, motors, valves and gearboxes. Our services range from large industrial plants to the individual that owns one piece of equipment. We also offer removal and install of cylinders. Along with free pick up and delivery, within a certain distance which is usually 100 miles from one of our shops.<br>With over 30 years experience in the hydraulic business, we can repair or replace any job. There is not a job too big or too small, we service them all.<br>We have customers that send whole pieces of equipment to us to do complete overhauls on all the hydraulics. Ranging from a country club green roller to a 10 ton boom truck.</p>
    <a class="btn">Read more</a>
  </section>

  <!-- services band -->
  <svg class="abs" style="left:0;top:1036px" width="1200" height="540" viewBox="0 0 1200 540">
    <defs>
      <linearGradient id="band" x1="0" y1="0" x2="0" y2="1">
        <stop offset="0" stop-color="#ec1f27"/>
        <stop offset="0.6" stop-color="#e31b23"/>
        <stop offset="1" stop-color="#ec1f27"/>
      </linearGradient>
    </defs>
    <polygon points="0,0 1200,104 1200,112 0,10" fill="#b5b5b5"/>
    <polygon points="0,10 1200,112 1200,532 0,440" fill="url(#band)" role="img" aria-label="Red band with a faint refinery reflection"/>
  </svg>

  <div class="services-head">
    <h2>SERVICES</h2>
    <p>Removal and install of cylinders</p>
  </div>
  <div class="job" role="img" aria-label="Yellow hydraulic cylinder strapped on a flatbed trailer" style="left:123px;background:linear-gradient(160deg,#b9b6ac,#8d8a80 55%,#5e5b55)"></div>
  <div class="job" role="img" aria-label="Two large grey cylinders on wooden blocks in a workshop" style="left:448px;background:linear-gradient(160deg,#4a4642,#a9a8a4 50%,#8c7a5e)"></div>
  <div class="job" role="img" aria-label="Four rebuilt cylinders standing on a pallet" style="left:772px;background:linear-gradient(160deg,#8f8e8a,#6f6d68 50%,#b8a07a)"></div>
  <svg class="arrow" style="left:82px;top:1312px" width="16" height="24" viewBox="0 0 16 24"><path d="M12 3 L4 12 L12 21" fill="none" stroke="#fff" stroke-width="3"/></svg>
  <svg class="arrow" style="left:1100px;top:1312px" width="16" height="24" viewBox="0 0 16 24"><path d="M4 3 L12 12 L4 21" fill="none" stroke="#fff" stroke-width="3"/></svg>

  <!-- blog -->
  <div class="abs" role="img" aria-label="Faint industrial silhouette behind the blog" style="left:0;top:1578px;width:1200px;height:470px;background:linear-gradient(180deg,rgba(255,255,255,0) 0%,#f1f1f1 70%,#e9e9e9 100%)"></div>
  <h2 class="blog-title">BLOG</h2>

  <article class="post" style="left:76px">
    <div class="post-photo" role="img" aria-label="Black cylinders lying on a workshop floor" style="background:linear-gradient(160deg,#9a9a98,#4d4d4f 55%,#7b7a76)">
      <div class="post-author">By: Marla</div>
      <div class="post-date"><div class="d">07</div><div class="m">FEB</div><div class="y">2018</div></div>
    </div>
    <p>Nulla sit quam massa elit amet. Laoreet dictum torquent diam elit vestibulum</p>
    <a class="btn">Read more</a>
  </article>

  <article class="post" style="left:438px">
    <div class="post-photo" role="img" aria-label="Orange painted cylinder beside a wooden crate" style="background:linear-gradient(160deg,#2d2d2d,#d8521e 45%,#b88a55 70%,#3a3a3a)">
      <div class="post-author">By: Tessa</div>
      <div class="post-date"><div class="d">20</div><div class="m">DEC</div><div class="y">2017</div></div>
    </div>
    <p>Nulla sit quam massa elit amet. Laoreet dictum torquent diam elit vestibulum</p>
    <a class="btn">Read more</a>
  </article>

  <article class="post" style="left:799px">
    <div class="post-photo" role="img" aria-label="Rust red cylinders resting on a pallet" style="background:linear-gradient(160deg,#8d8a84,#7d3a2c 50%,#a8927a)">
      <div class="post-author">By: Tessa</div>
      <div class="post-date"><div class="d">13</div><div class="m">JUN</div><div class="y">2017</div></div>
    </div>
    <p>Nulla sit quam massa elit amet. Laoreet dictum torquent diam elit vestibulum</p>
    <a class="btn">Read more</a>
  </article>

  <!-- footer -->
  <footer>
    <div class="footer-rule"></div>
    <div class="foot-brand"><span class="brand-dot"></span><span class="brand-name">BRACKENFORD<br>FLUIDWORKS</span></div>
    <div class="foot-address">
      <svg width="11" height="15" viewBox="0 0 11 15"><path d="M5.5 0C2.5 0 0 2.4 0 5.4 0 9.3 5.5 15 5.5 15S11 9.3 11 5.4C11 2.4 8.5 0 5.5 0Z" fill="#111"/><circle cx="5.5" cy="5.3" r="2" fill="#fff"/></svg>
      #123 Lorium ipsum<br>Dolor Amit, AU.
    </div>
    <div class="copyright">© 2018 &nbsp;|&nbsp; www.companyname.com</div>

    <div class="foot-col abs" style="left:345px;top:2106px">
      <h3>QUICK LINKS</h3>
      <ul class="links">
        <li>Home</li><li>About Us</li><li>Products</li><li>Blog</li><li>Contact Us</li>
      </ul>
    </div>

    <div class="foot-col abs" style="left:560px;top:2106px">
      <h3>NEWSLETTER</h3>
      <div class="email">Enter Email id
        <svg width="14" height="11" viewBox="0 0 14 11"><rect x="1" y="1" width="12" height="9" fill="none" stroke="#666" stroke-width="1.4"/><path d="M1 1 L7 6 L13 1" fill="none" stroke="#666" stroke-width="1.4"/></svg>
      </div>
      <a class="btn subscribe">SUBSCRIBE</a>
      <div class="foot-social">
        <span style="background:var(--navy)"></span>
        <span style="background:var(--sky)"></span>
        <span style="background:var(--red)"></span>
      </div>
    </div>

    <div class="foot-col abs" style="left:852px;top:2106px">
      <h3>ABOUT US</h3>
      <p class="about-text">Aliquip rutrum nulla. Porttitor rhoncus suspendisse. Augue enim ac donec donec turpis. Augue congue vel. Lacus tellus leo. Libero euismod ut. Justo</p>
      <a class="btn about-btn">Read more</a>
    </div>
  </footer>

</div>
</body>
</html>
```